Quorva - corporate Business Card

We need a good look and innovative business card for a new start up company based in Los Angeles called "Quorva". We are in a payment business, including payment card, app, and ewallet. We are expert in online payment and Card not present (CNP) transaction.
We need an innovative, modern business card.

Our logo font is Aero Matics

Target Market(s)

Startup - Bank - Online Payment - Card Manufacturing

Industry/Entity Type

Startup

Contact Information for Business Card

phone: 555 014 7396 - Address: 4172 Marlowe blvd, Calder City, CA 90299

Requirements
Must have
• Message: innovative, professional, expert, high tech, trust, online payment expert, security
Nice to have
• no comment
Should not have
• no Comment

```html
<!DOCTYPE html>
<html lang="en">
<head>
<meta charset="UTF-8">
<title>Quorva – Business Card</title>
<link rel="stylesheet" href="https://fonts.googleapis.com/css2?family=Source+Sans+3:wght@400;600;700&display=swap">
<style>
  :root {
    --stage: #000000;
    --card: #313235;
    --brand-red: #b51f2e;
    --text-light: #f1f1f1;
    --divider: #4a4b4f;
  }
  * { margin: 0; padding: 0; box-sizing: border-box; }
  html, body {
    width: 1200px; height: 900px; overflow: hidden;
    background: var(--stage);
    font-family: "Source Sans 3", "Myriad Pro", Arial, sans-serif;
  }
  .canvas { position: relative; width: 1200px; height: 900px; }
  .card {
    position: absolute; top: 271px;
    width: 457px; height: 281px;
    background: var(--card);
    border-radius: 14px;
  }
  .card--front { left: 137px; }
  .card--back { left: 626px; }

  .brand-disc {
    position: absolute; border-radius: 50%;
    background: var(--brand-red);
  }
  .card--front .brand-disc { left: 61px; top: 78px; width: 130px; height: 130px; }

  .divider {
    position: absolute; left: 230px; top: 79px;
    width: 1px; height: 120px; background: var(--divider);
  }
  .contact { position: absolute; left: 260px; top: 72px; color: var(--text-light); }
  .contact__name { color: var(--brand-red); font-weight: 600; font-size: 17px; line-height: 20px; }
  .contact__title { font-size: 13.5px; line-height: 16px; }
  .contact__list { list-style: none; margin-top: 23px; font-size: 13.5px; line-height: 17px; }
  .contact__list li { display: flex; align-items: center; gap: 5px; }
  .contact__list svg { width: 10px; height: 10px; fill: var(--brand-red); }
  .contact__address { margin-top: 17px; font-size: 13.5px; line-height: 17px; }

  .wordmark {
    position: absolute; left: 94px; top: 100px;
    display: flex; align-items: center; gap: 14px;
  }
  .wordmark .brand-disc { position: static; width: 80px; height: 80px; }
  .wordmark__name {
    color: var(--brand-red); font-weight: 600;
    font-size: 54px; letter-spacing: 2px; line-height: 1;
  }
</style>
</head>
<body>
<main class="canvas">
  <section class="card card--front" aria-label="Business card front">
    <div class="brand-disc" aria-hidden="true"></div>
    <div class="divider"></div>
    <div class="contact">
      <p class="contact__name">Daniel Hartwell</p>
      <p class="contact__title">Managing Director</p>
      <ul class="contact__list">
        <li>
          <svg viewBox="0 0 10 10" aria-hidden="true"><path d="M2 0.5 L3.6 2.6 L2.8 3.6 C3.4 5 4.8 6.5 6.3 7.1 L7.3 6.3 L9.5 7.9 L8.4 9.5 C4.5 9.2 0.8 5.4 0.5 1.6 Z"/></svg>
          555 014 7396
        </li>
        <li>
          <svg viewBox="0 0 10 10" aria-hidden="true"><circle cx="5" cy="5" r="4.6"/></svg>
          www.quorva.com
        </li>
      </ul>
      <p class="contact__address">4172 Marlowe blvd,<br>Calder City, CA 90299</p>
    </div>
  </section>

  <section class="card card--back" aria-label="Business card back">
    <div class="wordmark">
      <div class="brand-disc" aria-hidden="true"></div>
      <span class="wordmark__name">quorva</span>
    </div>
  </section>
</main>
</body>
</html>
```